Design the Business card for NetVaultic

Business card required for a professional Cyber Security business.
Company Logo and Icon has already been provided however I would like other options for the logo and icon to compare to. Alternatively, please refine/enhance the image of the logo.icon I have already provided.

If you are going to use the provided logo and icon, I was thinking that the company raised Logo on White background would serve well on the front of the card. See attached. AND, a large company raised stand-alone icon to appear on black background on the back of the card with tagline 'Cyber Risk Management, Governance and Consulting' or 'Cyber Security for your Business' See attached.
Alternatively, provide your own design for the logo and icon.

Target Market(s)

Enterprise, Government, Financial.

Contact Information for Business Card

Tavin Orloweth
Founder and CEO

Email Address
Mobile Number
Website URL
LinkedIn URL

Logo Text

NetVaultic - see attached example of logo

Font styles to use
Other font styles liked:
• Berlin Sans FB

Requirements
Must have
• Clean large and bold icon on the back with tagline.
• Horizontal alignment,
Nice to have
• Round edges.
• Raised Logo/Icon
Should not have
• An unprofessional look and feel.

```html
<!DOCTYPE html>
<html lang="en">
<head>
<meta charset="utf-8">
<title>NetVaultic Business Card</title>
<link rel="stylesheet" href="https://fonts.googleapis.com/css2?family=Roboto+Condensed:wght@500&family=Roboto:wght@400&family=Cabin:wght@500&display=swap">
<style>
  :root {
    --bg: #e9e6e1;
    --card: #1c1c1e;
    --blue: #0a72c4;
    --brand-blue: #4a6fc8;
    --yellow: #ffc20e;
    --text: #f2f2f2;
    --divider: #55575c;
  }
  * { margin: 0; padding: 0; box-sizing: border-box; }
  html, body { width: 1200px; height: 960px; overflow: hidden; background: var(--bg); }
  .canvas { position: relative; width: 1200px; height: 960px; }
  .card {
    position: absolute;
    width: 600px; height: 342px;
    background: var(--card);
    box-shadow: 0 3px 8px rgba(0,0,0,.35);
    overflow: hidden;
  }
  .card--front { left: 314px; top: 114px; }
  .card--back { left: 311px; top: 472px; height: 343px; }
  .band { position: absolute; left: 0; width: 100%; }
  .band--top { top: 0; height: 16px; background: var(--blue); }
  .band--bottom { bottom: 0; height: 17px; background: var(--yellow); }

  .brand {
    position: absolute; left: 69px; top: 146px;
    display: flex; align-items: center; gap: 10px;
  }
  .brand__dot { width: 40px; height: 40px; border-radius: 50%; background: var(--brand-blue); }
  .brand__name {
    font-family: "Cabin", sans-serif; font-weight: 500;
    font-size: 33px; color: var(--blue); letter-spacing: .2px;
  }
  .divider {
    position: absolute; left: 327px; top: 86px;
    width: 1px; height: 156px; background: var(--divider);
  }
  .contact { position: absolute; left: 355px; top: 96px; }
  .contact__name {
    font-family: "Roboto Condensed", sans-serif; font-weight: 500;
    font-size: 22px; color: var(--blue); line-height: 1; letter-spacing: .3px;
  }
  .contact__title {
    font-family: "Roboto Condensed", sans-serif; font-weight: 500;
    font-size: 15px; color: var(--yellow); margin-top: 5px; letter-spacing: .3px;
  }
  .contact__list { list-style: none; margin-top: 17px; }
  .contact__item {
    display: flex; align-items: center; gap: 10px;
    font-family: "Roboto", sans-serif; font-size: 14.5px;
    color: var(--text); height: 19px;
  }
  .contact__icon { width: 13px; height: 13px; flex: none; }

  .emblem {
    position: absolute; left: 50%; top: 58px; transform: translateX(-50%);
    display: flex; flex-direction: column; align-items: center; gap: 14px;
  }
  .emblem__dot { width: 150px; height: 150px; border-radius: 50%; background: var(--brand-blue); }
  .emblem__name {
    font-family: "Cabin", sans-serif; font-weight: 500;
    font-size: 24px; color: var(--brand-blue);
  }
  .tagline {
    position: absolute; left: 0; right: 0; top: 276px; text-align: center;
    font-family: "Cabin", sans-serif; font-weight: 500; font-size: 18px;
  }
  .tagline__lead { color: var(--brand-blue); }
  .tagline__tail { color: var(--yellow); }
</style>
</head>
<body>
<main class="canvas">
  <section class="card card--front" aria-label="Card front">
    <div class="band band--top"></div>
    <div class="brand">
      <span class="brand__dot"></span>
      <span class="brand__name">NetVaultic</span>
    </div>
    <div class="divider"></div>
    <div class="contact">
      <h1 class="contact__name">TAVIN ORLOWETH</h1>
      <p class="contact__title">FOUNDER &amp; CEO</p>
      <ul class="contact__list">
        <li class="contact__item">
          <svg class="contact__icon" viewBox="0 0 13 13" aria-hidden="true"><rect x="3" y="0.5" width="7" height="12" rx="1.5" fill="none" stroke="#0a72c4" stroke-width="1.6"/><rect x="5.5" y="10" width="2" height="1" fill="#0a72c4"/></svg>
          555 014 2290
        </li>
        <li class="contact__item">
          <svg class="contact__icon" viewBox="0 0 13 13" aria-hidden="true"><rect x="0.5" y="2.5" width="12" height="8" fill="#0a72c4"/><path d="M0.5 2.5 L6.5 7 L12.5 2.5" fill="none" stroke="#1c1c1e" stroke-width="1.2"/></svg>
          tavin@netvaultic.com
        </li>
        <li class="contact__item">
          <svg class="contact__icon" viewBox="0 0 13 13" aria-hidden="true"><circle cx="6.5" cy="6.5" r="6" fill="#0a72c4"/><path d="M3 4 Q5 3 6 5 T9 9 M7 2 Q9 3 10 5" fill="none" stroke="#1c1c1e" stroke-width="1.2"/></svg>
          www.netvaultic.com
        </li>
        <li class="contact__item">
          <svg class="contact__icon" viewBox="0 0 13 13" aria-hidden="true"><circle cx="6.5" cy="6.5" r="6" fill="#0a72c4"/></svg>
          netvaultic
        </li>
      </ul>
    </div>
    <div class="band band--bottom"></div>
  </section>

  <section class="card card--back" aria-label="Card back">
    <div class="emblem">
      <span class="emblem__dot"></span>
      <span class="emblem__name">NetVaultic</span>
    </div>
    <p class="tagline"><span class="tagline__lead">Cyber Risk Management,</span> <span class="tagline__tail">Governance &amp; Consulting</span></p>
  </section>
</main>
</body>
</html>
```